gtw school poster design and change logo name

We already have a logo which only needs to be slightly modified with "school".
We also have two advertising faces, a girl and a boy, which should be on our poster.
Important key data:

bilingual D/E small classes
daycare
private kindergarten
private school from 2024

Poster size: 268,5 x 128 cm
We need logo sizes in different sizes
also for T-shirts.
Attached also a old poster

new clients

0094D4
00A9DD
6FCCEA
C7EBF8
E9F6FB
59FF00
82FF00
B8FF75
E3FFCB
F4FFEA
FFC000
F8CF3A
FAE287
FDF2CF
FEFAEE
F0912C
F2A743
F7CA91
FBE8D2
FDF5EE

```html
<!DOCTYPE html>
<html lang="de">
<head>
<meta charset="utf-8">
<title>gtw school – Kindertagesstätte Banner</title>
<link href="https://fonts.googleapis.com/css2?family=Poppins:wght@400;500;600;700&display=swap" rel="stylesheet">
<style>
  :root {
    --stage: #e6e6e6;
    --white: #ffffff;
    --orange: #fdab03;
    --orange-deep: #f0912c;
    --pink: #f4489c;
    --blue: #139fdc;
    --blue-tab: #0ea2d8;
    --lime: #b8d20c;
    --ink: #2a2a2a;
    --splash-green: #59c21a;
    --splash-magenta: #c93bd8;
  }
  * { box-sizing: border-box; margin: 0; padding: 0; }
  html, body {
    width: 1200px; height: 800px; overflow: hidden;
    background: var(--stage);
    font-family: "Poppins", sans-serif;
    color: var(--ink);
  }
  .banner {
    position: absolute; left: 0; top: 114px;
    width: 1200px; height: 572px;
    background: var(--white);
    overflow: hidden;
  }
  .banner-shapes { position: absolute; inset: 0; }
  .abs { position: absolute; line-height: 1; white-space: nowrap; }

  .splash { position: absolute; border-radius: 50%; }
  .splash-green { left: -20px; top: -25px; width: 80px; height: 90px; background: var(--splash-green); }
  .splash-orange { left: 300px; top: -20px; width: 75px; height: 110px; background: var(--orange-deep); border-radius: 45%; }
  .splash-magenta { left: 1075px; top: -10px; width: 95px; height: 85px; background: var(--splash-magenta); }
  .splash-blue-top { left: 1182px; top: 30px; width: 30px; height: 40px; background: var(--blue); }
  .splash-blue-bottom { left: 1150px; top: 520px; width: 70px; height: 70px; background: var(--blue); }

  .brand { left: 38px; top: 108px; width: 220px; text-align: center; }
  .brand-name { font-size: 38px; font-weight: 700; color: var(--ink); line-height: 1; }

  .thought { position: absolute; left: 50px; top: 238px; width: 210px; height: 128px; }
  .thought-text { left: 83px; top: 268px; }
  .thought-small { display: block; font-size: 13px; font-weight: 500; }
  .thought-big { display: block; font-size: 29px; font-weight: 700; margin-top: 1px; }

  .kids-photo {
    position: absolute; left: 0; top: 358px; width: 460px; height: 214px;
    background: linear-gradient(90deg, #5fb5e0 0%, #e9b99a 35%, #f3d4bf 60%, #e9c7b0 85%, rgba(253,171,3,0) 100%);
    border-radius: 60px 80px 0 0;
  }

  .kicker { left: 435px; top: 42px; font-size: 37px; font-weight: 600; color: var(--ink); }
  .headline { left: 432px; top: 88px; font-size: 68px; font-weight: 700; color: var(--white); }
  .subline { left: 432px; top: 163px; font-size: 55px; font-weight: 700; color: var(--white); }
  .lead { left: 435px; top: 241px; font-size: 25px; font-weight: 500; line-height: 29px; }

  .pill {
    position: absolute; top: 329px; height: 41px; border-radius: 21px;
    background: var(--lime); border: 2px solid var(--ink);
    box-shadow: 0 3px 0 rgba(0,0,0,0.25);
    font-size: 27px; font-weight: 500; line-height: 37px; text-align: center;
  }
  .pill-care { left: 436px; width: 291px; }
  .pill-age { left: 750px; width: 291px; }

  .age-button {
    position: absolute; left: 438px; top: 401px; width: 449px; height: 59px;
    background: var(--blue); border: 2px solid var(--ink); border-radius: 8px;
    font-size: 44px; font-weight: 500; line-height: 52px; text-align: center;
  }

  .school-note { right: 123px; top: 400px; font-size: 21px; font-weight: 700; line-height: 20px; text-align: right; }
  .year-tab {
    position: absolute; left: 1086px; top: 368px; width: 114px; height: 102px;
    background: var(--blue-tab); border-radius: 30px 0 0 30px;
    color: var(--white); font-size: 44px; font-weight: 600; line-height: 42px;
    text-align: center; padding-top: 8px;
  }

  .phone-icon { position: absolute; left: 433px; top: 496px; width: 38px; height: 38px; }
  .phone-number { left: 482px; top: 494px; font-size: 41px; font-weight: 600; }

  .contact-icon { position: absolute; width: 18px; height: 18px; }
  .pin-icon { left: 833px; top: 489px; }
  .web-icon { left: 833px; top: 520px; }
  .address { left: 860px; top: 492px; font-size: 15px; font-weight: 500; }
  .website { left: 860px; top: 522px; font-size: 15px; font-weight: 500; letter-spacing: 2px; }
</style>
</head>
<body>
  <main class="banner">
    <svg class="banner-shapes" width="1200" height="572" viewBox="0 0 1200 572">
      <defs>
        <clipPath id="orange-field">
          <path d="M420,0 C340,150 282,330 270,572 L1200,572 L1200,0 Z"/>
        </clipPath>
      </defs>
      <path d="M420,0 C340,150 282,330 270,572 L1200,572 L1200,0 Z" fill="var(--orange)"/>
      <path d="M410,-4 C355,95 310,180 282,250" fill="none" stroke="var(--blue)" stroke-width="9" stroke-linecap="round"/>
      <rect x="0" y="157" width="1200" height="68" fill="var(--pink)" clip-path="url(#orange-field)"/>
    </svg>

    <div class="splash splash-green" role="img" aria-label="Green paint splash"></div>
    <div class="splash splash-orange" role="img" aria-label="Orange paint splash"></div>
    <div class="splash splash-magenta" role="img" aria-label="Magenta paint splash"></div>
    <div class="splash splash-blue-top" role="img" aria-label="Blue paint splash"></div>
    <div class="splash splash-blue-bottom" role="img" aria-label="Blue paint splash"></div>

    <div class="abs brand">
      <div class="brand-name">gtw school</div>
    </div>

    <svg class="thought" viewBox="0 0 210 128">
      <ellipse cx="98" cy="58" rx="92" ry="52" fill="var(--white)" stroke="var(--ink)" stroke-width="3"/>
      <circle cx="178" cy="106" r="9" fill="var(--white)" stroke="var(--ink)" stroke-width="3"/>
      <circle cx="198" cy="120" r="5" fill="var(--white)" stroke="var(--ink)" stroke-width="3"/>
    </svg>
    <div class="abs thought-text">
      <span class="thought-small">DO YOU SPEAK</span>
      <span class="thought-big">ENGLISH?</span>
    </div>

    <div class="kids-photo" role="img" aria-label="Photo of a laughing boy and a smiling girl showing paint-covered hands"></div>

    <h2 class="abs kicker">Zweisprachige D/E-Kleinklassen</h2>
    <h1 class="abs headline">KINDERTAGESSTÄTTE</h1>
    <p class="abs subline">PRIVATE KINDERGARTEN</p>
    <p class="abs lead">Bei uns lernen ALLE Kinder spielend einfach in kürzester<br>Zeit Englisch wie eine 2.Muttersprache.</p>

    <div class="pill pill-care">Kinderkrippe &amp; Hort</div>
    <div class="pill pill-age">Ab 3.Lebensmonat</div>
    <div class="age-button">bis zum lebensjahr</div>

    <p class="abs school-note">PRIVATGELÄNDE<br>SCHULE<br>AUS</p>
    <div class="year-tab">20<br>24</div>

    <svg class="phone-icon" viewBox="0 0 24 24" aria-hidden="true">
      <path d="M6.6 10.8a15 15 0 0 0 6.6 6.6l2.2-2.2a1 1 0 0 1 1-.25 11.4 11.4 0 0 0 3.6.57 1 1 0 0 1 1 1V20a1 1 0 0 1-1 1A17 17 0 0 1 3 4a1 1 0 0 1 1-1h3.5a1 1 0 0 1 1 1c0 1.25.2 2.45.57 3.57a1 1 0 0 1-.25 1z" fill="var(--pink)"/>
      <path d="M14 3.5a7 7 0 0 1 6.5 6.5M14 6.8a3.8 3.8 0 0 1 3.2 3.2" fill="none" stroke="var(--pink)" stroke-width="1.6" stroke-linecap="round"/>
    </svg>
    <p class="abs phone-number">+41 79 000 42 18</p>

    <svg class="contact-icon pin-icon" viewBox="0 0 24 24" aria-hidden="true">
      <path d="M12 2a7 7 0 0 0-7 7c0 5 7 13 7 13s7-8 7-13a7 7 0 0 0-7-7zm0 9.5A2.5 2.5 0 1 1 12 6.5a2.5 2.5 0 0 1 0 5z" fill="var(--pink)"/>
    </svg>
    <p class="abs address">Lindenweg 12, 8400 Talwil</p>

    <svg class="contact-icon web-icon" viewBox="0 0 24 24" aria-hidden="true">
      <circle cx="12" cy="12" r="9" fill="none" stroke="var(--pink)" stroke-width="2"/>
      <path d="M3 12h18M12 3c3 3 3 15 0 18M12 3c-3 3-3 15 0 18" fill="none" stroke="var(--pink)" stroke-width="1.6"/>
    </svg>
    <p class="abs website">www.gtw-kindertagesstätte.ch</p>
  </main>
</body>
</html>
```